Executive Business Card for Healthcare Company [Need Today]

I need a business card design for a healthcare company. The only branding the company has thus far is a logo. The cards will be utilized by company executives. The design I envision will be vibrant and appealing but with a corporate feel. They shouldn't be too casual or playful. I would like to complete this project TODAY if possible.

Target Market(s)

Healthcare vendors, other executives in healthcare and pharmaceuticals

Industry/Entity Type

Pharmaceutical

Contact Information for Business Card

See attachment

Font styles to use
Serif
Sans Serif

Colors

Designer to choose colors to be used in the design.

```html
<!DOCTYPE html>
<html lang="en">
<head>
<meta charset="utf-8">
<title>Verano Therapeutics – Business Card</title>
<link rel="stylesheet" href="https://fonts.googleapis.com/css2?family=Roboto:wght@300;400;500&display=swap">
<style>
  :root {
    --backdrop: #3b3b3c;
    --card: #1c1c1e;
    --card-edge: #2a2a2c;
    --emboss: #4a4a4d;
    --emboss-text: #6c6c70;
    --teal: #2bb3c4;
    --green: #45c08f;
    --accent-grey: #8a8a8f;
    --ink: #ececec;
    --ink-soft: #bdbdc2;
  }
  * { box-sizing: border-box; margin: 0; padding: 0; }
  html, body { width: 799px; height: 1200px; overflow: hidden; }
  body {
    background: var(--backdrop);
    font-family: "Roboto", Arial, sans-serif;
    position: relative;
  }
  .card {
    position: absolute;
    left: 90px;
    width: 620px;
    height: 354px;
    background: var(--card);
    border: 1px solid var(--card-edge);
    box-shadow: 0 12px 30px rgba(0,0,0,.45);
    overflow: hidden;
  }
  .card--front { top: 130px; }
  .card--back { top: 700px; }

  /* brand lockup */
  .brand {
    position: absolute;
    display: flex;
    align-items: center;
    gap: 18px;
  }
  .brand__mark {
    width: 96px; height: 96px;
    border-radius: 50%;
    border: 3px solid currentColor;
  }
  .brand__rule {
    width: 1px; height: 58px;
    background: currentColor;
    opacity: .7;
  }
  .brand__name {
    font-weight: 300;
    font-size: 44px;
    line-height: 1;
    letter-spacing: 1px;
  }
  .card--front .brand { left: 60px; top: 100px; color: var(--emboss-text); }
  .card--front .brand__mark { border-color: var(--emboss); }
  .card--front .brand__rule { background: var(--emboss); }

  .site {
    position: absolute;
    left: 60px; bottom: 50px;
    font-size: 19px;
    letter-spacing: 3px;
    color: var(--ink-soft);
  }

  /* back side */
  .side-band {
    position: absolute;
    left: 0; top: 0; bottom: 0;
    width: 48px;
    background: linear-gradient(180deg, var(--teal), var(--green));
  }
  .side-rule {
    position: absolute;
    left: 48px; top: 0; bottom: 0;
    width: 8px;
    background: var(--accent-grey);
  }
  .card--back .brand { left: 100px; top: 36px; color: var(--teal); }
  .card--back .brand__mark { width: 84px; height: 84px; border-color: var(--green); }
  .card--back .brand__rule { background: var(--accent-grey); }
  .card--back .brand__name { font-size: 40px; }

  .person { position: absolute; left: 100px; top: 150px; }
  .person__name { font-size: 24px; font-weight: 500; color: var(--teal); }
  .person__title { font-size: 13px; color: var(--ink-soft); margin-top: 3px; }

  .contact { position: absolute; left: 100px; top: 212px; list-style: none; }
  .contact__item {
    display: flex; align-items: center; gap: 8px;
    font-size: 15px; color: var(--ink);
    margin-bottom: 5px;
  }
  .contact__icon { width: 13px; height: 13px; fill: var(--teal); flex: none; }
  .contact__item--address { margin-top: 4px; }
</style>
</head>
<body>

<section class="card card--front" aria-label="Card front">
  <div class="brand">
    <div class="brand__mark"></div>
    <div class="brand__rule"></div>
    <div class="brand__name">verano therapeutics</div>
  </div>
  <div class="site">www.veranorx.com</div>
</section>

<section class="card card--back" aria-label="Card back">
  <div class="side-band"></div>
  <div class="side-rule"></div>

  <div class="brand">
    <div class="brand__mark"></div>
    <div class="brand__rule"></div>
    <div class="brand__name">verano therapeutics</div>
  </div>

  <div class="person">
    <div class="person__name">Daniel Marsh</div>
    <div class="person__title">Senior Director of Marketing</div>
  </div>

  <ul class="contact">
    <li class="contact__item">
      <svg class="contact__icon" viewBox="0 0 16 16" aria-hidden="true"><path d="M3 1h3l1.5 4-2 1.3a9 9 0 0 0 4.2 4.2L11 8.5l4 1.5v3a2 2 0 0 1-2 2A12 12 0 0 1 1 3a2 2 0 0 1 2-2z"/></svg>
      555-010-4821
    </li>
    <li class="contact__item">
      <svg class="contact__icon" viewBox="0 0 16 16" aria-hidden="true"><path d="M4 0h8a1 1 0 0 1 1 1v14a1 1 0 0 1-1 1H4a1 1 0 0 1-1-1V1a1 1 0 0 1 1-1zm1 2v10h6V2zm3 11a1 1 0 1 0 0 2 1 1 0 0 0 0-2z"/></svg>
      555-010-7364
    </li>
    <li class="contact__item">
      <svg class="contact__icon" viewBox="0 0 16 16" aria-hidden="true"><path d="M8 0a8 8 0 1 0 0 16A8 8 0 0 0 8 0zm5.9 7h-2.9a12 12 0 0 0-1-4.8A6 6 0 0 1 13.9 7zM8 2c.8 1 1.4 2.9 1.5 5h-3C6.6 4.9 7.2 3 8 2zM6 2.2A12 12 0 0 0 5 7H2.1A6 6 0 0 1 6 2.2zM2.1 9H5a12 12 0 0 0 1 4.8A6 6 0 0 1 2.1 9zM8 14c-.8-1-1.4-2.9-1.5-5h3c-.1 2.1-.7 4-1.5 5zm2 -.2A12 12 0 0 0 11 9h2.9a6 6 0 0 1-3.9 4.8z"/></svg>
      dmarsh@veranorx.com
    </li>
    <li class="contact__item contact__item--address">118 W Oak Avenue Dalton, GA 30720</li>
  </ul>
</section>

</body>
</html>
```